Save The Date for 2019 LCS Symposium

We have an annual meeting each June and need a Save the Date (STD) designed. It should be a two-sided postcard with room for address and stamp (according to Kestrel Post postal standards). I have attached some examples from prior years, but we would appreciate a more modern and attractive design for this year's STD.

Target Market(s)

Our own members - nurses, nurse practitioners, PAs and physicians

Industry/Entity Type

Medical

Requirements
Must have
• Must include our logos (attached), ideally in a coordinating fashion - as was done in prior years (see examples attached) and without modifying the logos too much. Needs have the following information:
• - "Save the Date"
• - "The 12th Annual Linwood Clinical Summit"
• - "Friday, June 7, 2019" or "6/7/19"
• - "The Harrowgate Pell Building | 318 West 67th Street | NYC"
• - Please include our website (www.brelmar-hq.org/events), phone number (555-310-4472) and email address (ask@brelmar-hq.org) for people to ask questions
• - Must have space for a postage stamp and the name/address of the postcard recipient
Nice to have
• Would be nice to remain in our blue/grey/olive color palate (see attached Brand Standards guide).
Should not have
• Please do not use stock photos of medical staff. Please don't use cartoons or cartoon images (although a tasteful sketch may be considered).

```html
<!DOCTYPE html>
<html lang="en">
<head>
<meta charset="utf-8">
<title>Save the Date – Linwood Clinical Summit 2019</title>
<link rel="stylesheet" href="https://fonts.googleapis.com/css2?family=EB+Garamond:ital,wght@0,400;0,500;0,700;1,400&display=swap">
<style>
  :root {
    --backdrop: #bbbdbf;
    --paper: #ffffff;
    --card-blue: #bed4e8;
    --navy: #1b3566;
    --sketch-blue: #6faad6;
    --sketch-pale: #a9cbe6;
    --write-panel: rgba(255,255,255,0.76);
  }
  * { box-sizing: border-box; margin: 0; padding: 0; }
  html, body {
    width: 892px; height: 1200px; overflow: hidden;
    background: var(--backdrop);
  }
  body { font-family: "EB Garamond", Georgia, serif; color: var(--navy); }
  .stage {
    position: absolute; left: 0; top: 0;
    width: 1108px; height: 1490px;
    transform: scale(0.805); transform-origin: 0 0;
  }
  .postcard {
    position: absolute; left: 140px; width: 805px; height: 575px;
    background: var(--paper);
  }
  .postcard--front { top: 82px; }
  .postcard--back { top: 810px; }
  .postcard__field {
    position: absolute; left: 29px; top: 28px; width: 747px; height: 518px;
    background: var(--card-blue); overflow: hidden;
  }
  .abs { position: absolute; }

  /* front */
  .date-stack { left: 22px; top: 18px; width: 28px; text-align: center; font-size: 24px; font-weight: 500; line-height: 1; }
  .date-stack span { display: block; padding: 5px 0 6px; }
  .date-stack span + span { border-top: 1.5px solid var(--navy); }
  .sketch {
    background: radial-gradient(ellipse at 50% 45%, var(--sketch-blue) 0%, var(--sketch-pale) 55%, rgba(190,212,232,0) 75%);
    opacity: .75;
  }
  .sketch--front { left: 190px; top: 10px; width: 370px; height: 400px; }
  .event-title { left: 0; top: 142px; width: 747px; text-align: center; font-size: 16px; font-style: italic; }
  .venue { left: 0; width: 747px; text-align: center; font-size: 19px; line-height: 1.2; }
  .venue--name { top: 173px; }
  .venue--street { top: 252px; }
  .headline {
    left: 0; top: 190px; width: 747px; text-align: center;
    font-size: 62px; font-weight: 700; letter-spacing: 14px; line-height: 1;
    padding-left: 14px;
  }
  .headline small { font-size: 19px; letter-spacing: 4px; margin: 0 22px 0 14px; vertical-align: 0.8em; }
  .divider { left: 34px; top: 432px; width: 677px; height: 0; border-top: 1.5px solid var(--navy); }
  .partner { top: 450px; display: flex; align-items: center; gap: 18px; font-size: 11px; line-height: 1.35; }
  .partner__badge { width: 46px; height: 46px; border-radius: 50%; border: 2px solid var(--navy); flex: none; }
  .partner em { display: block; }
  .partner--host { left: 33px; }
  .partner--chapter { left: 265px; }
  .partner--center { left: 520px; }
  .contact-line { right: 30px; bottom: 12px; font-size: 10px; font-style: italic; white-space: nowrap; }

  /* back */
  .sketch--back { left: 20px; top: 10px; width: 440px; height: 490px; }
  .message-panel { left: 43px; top: 52px; width: 350px; height: 420px; background: var(--write-panel); }
  .return-address { left: 445px; top: 35px; display: flex; align-items: center; gap: 8px; }
  .return-address__badge { width: 38px; height: 38px; border-radius: 50%; background: var(--navy); }
  .return-address__text { border-left: 1px solid var(--navy); padding-left: 7px; line-height: 1.1; }
  .return-address__org { font-size: 15px; }
  .return-address__tag { font-size: 6px; font-weight: 700; letter-spacing: .5px; }
  .return-address__line { font-size: 6.5px; }
  .stamp-box { left: 650px; top: 28px; width: 69px; height: 74px; background: var(--paper); }
  .address-line { left: 490px; width: 229px; height: 36px; background: var(--paper); }
</style>
</head>
<body>
<div class="stage">

  <section class="postcard postcard--front">
    <div class="postcard__field">
      <div class="abs date-stack"><span>06</span><span>07</span><span>19</span></div>
      <div class="abs sketch sketch--front" role="img" aria-label="Engraved sketch of an anatomical heart surrounded by roses and leaves"></div>
      <p class="abs event-title">The 12th Annual Linwood Clinical Summit</p>
      <p class="abs venue venue--name">The Harrowgate Pell Building</p>
      <h1 class="abs headline">SAVE<small>THE</small>DATE</h1>
      <p class="abs venue venue--street">318 West 67th Street, NYC</p>
      <div class="abs divider"></div>
      <div class="abs partner partner--host">
        <div class="partner__badge"></div>
        <p><em>Presented by</em>The Ashfield<br>Cardiological Society, Inc.</p>
      </div>
      <div class="abs partner partner--chapter">
        <div class="partner__badge"></div>
        <p><em>of the</em>Eastland State Chapter,<br>Brelmar College of Cardiology</p>
      </div>
      <div class="abs partner partner--center">
        <div class="partner__badge"></div>
        <p><em>In association with</em>Ashfield Cardiac Center</p>
      </div>
    </div>
    <p class="abs contact-line">For additional information visit www.brelmar-hq.org/events, call 555.310.4472 or email ask@brelmar-hq.org</p>
  </section>

  <section class="postcard postcard--back">
    <div class="postcard__field">
      <div class="abs sketch sketch--back" role="img" aria-label="Faint engraved sketch of an anatomical heart with roses"></div>
      <div class="abs message-panel"></div>
      <div class="abs return-address">
        <div class="return-address__badge"></div>
        <div class="return-address__text">
          <p class="return-address__org">Eastland State</p>
          <p class="return-address__tag">CHAPTER</p>
          <p class="return-address__line">412 Ferris Avenue, Ste. 1902</p>
          <p class="return-address__line">Ashfield, ST 20418</p>
        </div>
      </div>
      <div class="abs stamp-box"></div>
      <div class="abs address-line" style="top:199px"></div>
      <div class="abs address-line" style="top:245px"></div>
      <div class="abs address-line" style="top:292px"></div>
    </div>
  </section>

</div>
</body>
</html>
```